Elegant Business Card for Technology Company

Client is a supplier of innovative industrial communications and automation equipment since 2002. This contest is to gather fresh ideas for a redesign of the existing business card. Client is looking for design that best communicates tagline "Industrial Networking and Computing Specialist".

Design submissions should look modern, clean, elegant and professional. It should not be cluttered. Use white as the primary colour. Orange and black as secondary colour. Refer to jpeg File 1 on the current design.

Fonts used by Client used include Arial Regular, Arial Black, Roboto Regular, Roboto Black and Lato.

The winning design will be sent for offset printing using super white 250gsm artcard paper (open for suggestions).

Target Market(s)

System Engineers, Project Managers, Purchasing Managers from companies providing engineering services for Smart Cities.

Industry/Entity Type

Information Technology

Contact Information for Business Card

Refer to PDF File 3 for Business Card Details. Priority of short contact information would be as follows Name > Job Title > Email > Mobile > Web > Tel > Fax > Business Address >UEN (UEN represents company registration number)

Font styles to use
Sans Serif

Colors
ffffff
f37122
000000
5c5c5c

Requirements
Must have
• Refer to AI File 2 (Company Logo) & PDF File 3 (Information on Namecard)
Should not have
• No QR codes
• No Social Media Icons
• Do not create full Black or Orange colour background

```html
<!DOCTYPE html>
<html lang="en">
<head>
<meta charset="utf-8">
<title>Orvix Business Card</title>
<link href="https://fonts.googleapis.com/css2?family=Roboto:wght@400;500;700;900&display=swap" rel="stylesheet">
<style>
  :root {
    --white: #ffffff;
    --orange: #f37122;
    --black: #000000;
    --grey: #5c5c5c;
    --backdrop: #e6e6e6;
  }
  * { margin: 0; padding: 0; box-sizing: border-box; }
  html, body { width: 1200px; height: 900px; overflow: hidden; }
  body {
    background: var(--backdrop);
    font-family: "Roboto", Arial, sans-serif;
    position: relative;
  }
  .card {
    position: absolute;
    left: 330px;
    width: 540px;
    height: 310px;
    background: var(--white);
    border-radius: 18px;
    overflow: hidden;
    box-shadow: 0 8px 24px rgba(0,0,0,0.18);
  }
  .card-front { top: 90px; }
  .card-back { top: 470px; }
  .card-shape { position: absolute; inset: 0; width: 100%; height: 100%; }

  /* front */
  .front-brand {
    position: absolute;
    top: 52px; left: 0; right: 0;
    display: flex; align-items: center; justify-content: center; gap: 14px;
  }
  .brand-dot {
    width: 54px; height: 54px; border-radius: 50%;
    background: var(--white);
  }
  .front-brand .brand-name {
    font-weight: 900; font-size: 58px; letter-spacing: 2px; color: var(--black);
  }
  .tagline {
    position: absolute; top: 140px; left: 0; right: 0;
    text-align: center; color: var(--white);
    font-size: 15px; font-weight: 500; letter-spacing: 0.6px; text-transform: uppercase;
  }
  .services {
    position: absolute; top: 170px; left: 0; right: 0;
    list-style: none; text-align: center;
    color: var(--black); font-size: 14px; font-weight: 500; line-height: 18px;
  }

  /* back */
  .divider {
    position: absolute; left: 200px; right: 30px; top: 118px;
    height: 1.5px; background: var(--black);
  }
  .person { position: absolute; left: 34px; top: 94px; }
  .person-name { font-size: 22px; font-weight: 900; color: var(--black); letter-spacing: 0.5px; }
  .person-title { font-size: 14px; font-weight: 500; color: var(--orange); letter-spacing: 0.5px; text-transform: uppercase; }
  .address {
    position: absolute; left: 34px; top: 150px;
    font-size: 12.5px; line-height: 16px; color: var(--black);
  }
  .contacts {
    position: absolute; left: 34px; top: 188px;
    list-style: none; font-size: 12.5px; line-height: 17px; color: var(--black);
  }
  .contacts li { display: flex; align-items: center; gap: 8px; }
  .contacts svg { width: 11px; height: 11px; flex: none; }
  .back-brand {
    position: absolute; right: 34px; top: 145px;
    display: flex; flex-direction: column; align-items: flex-end;
  }
  .back-brand .brand-row { display: flex; align-items: center; gap: 10px; }
  .back-brand .brand-dot { width: 40px; height: 40px; background: var(--orange); }
  .back-brand .brand-name { font-weight: 900; font-size: 42px; letter-spacing: 2px; color: var(--black); }
  .company { margin-top: 4px; font-size: 12.5px; font-weight: 700; color: var(--black); text-transform: uppercase; }
  .company .accent { color: var(--orange); }
  .uen { font-size: 12px; color: var(--black); }
  .uen .accent { color: var(--orange); }
</style>
</head>
<body>

<section class="card card-front" aria-label="Card front">
  <svg class="card-shape" viewBox="0 0 540 310" preserveAspectRatio="none" aria-hidden="true">
    <polygon points="0,22 540,0 540,272 0,296" fill="var(--orange)"/>
  </svg>
  <div class="front-brand">
    <span class="brand-dot"></span>
    <span class="brand-name">ORVIX</span>
  </div>
  <p class="tagline">Industrial Networking and Computing Specialist</p>
  <ul class="services">
    <li>Industrial Ethernet / Wireless / Cellular</li>
    <li>Industrial and Embedded Computing</li>
    <li>Serial / Fieldbus Connectivity</li>
    <li>IP Video Surveillance</li>
    <li>Remote Automation</li>
  </ul>
</section>

<section class="card card-back" aria-label="Card back">
  <svg class="card-shape" viewBox="0 0 540 310" preserveAspectRatio="none" aria-hidden="true">
    <polygon points="0,92 420,0 540,0 540,6 0,124" fill="var(--orange)"/>
    <polygon points="540,250 540,310 260,310" fill="var(--orange)"/>
  </svg>
  <div class="divider"></div>
  <div class="person">
    <p class="person-name">DANIEL KOH</p>
    <p class="person-title">Sales Manager</p>
  </div>
  <p class="address">22 Kallang Way Tech Hub #04-12<br>(Block B), Singapore 349581</p>
  <ul class="contacts">
    <li><svg viewBox="0 0 12 12"><rect x="3" y="0.5" width="6" height="11" rx="1.2" fill="none" stroke="var(--orange)" stroke-width="1.4"/></svg>+65 9123 4567</li>
    <li><svg viewBox="0 0 12 12"><path d="M2 1 L4.5 1 L5.5 4 L4 5 Q5 7.5 7 8 L8 6.5 L11 7.5 L11 10 Q6 11.5 1 3.5 Z" fill="var(--orange)"/></svg>+65 6234 5510</li>
    <li><svg viewBox="0 0 12 12"><rect x="1" y="4" width="10" height="6" rx="1" fill="var(--orange)"/><rect x="3" y="1" width="6" height="3" fill="var(--orange)"/></svg>+65 6234 5511</li>
    <li><svg viewBox="0 0 12 12"><rect x="0.7" y="2.2" width="10.6" height="7.6" fill="none" stroke="var(--orange)" stroke-width="1.3"/><path d="M1 2.5 L6 6.5 L11 2.5" fill="none" stroke="var(--orange)" stroke-width="1.3"/></svg>sales@orvix.com.sg</li>
    <li><svg viewBox="0 0 12 12"><circle cx="6" cy="6" r="5" fill="none" stroke="var(--orange)" stroke-width="1.3"/><ellipse cx="6" cy="6" rx="2.2" ry="5" fill="none" stroke="var(--orange)" stroke-width="1"/><line x1="1" y1="6" x2="11" y2="6" stroke="var(--orange)" stroke-width="1"/></svg>www.orvix.com.sg</li>
  </ul>
  <div class="back-brand">
    <div class="brand-row">
      <span class="brand-dot"></span>
      <span class="brand-name">ORVIX</span>
    </div>
    <p class="company"><span class="accent">Orvix</span> Asia Pacific Pte Ltd</p>
    <p class="uen"><span class="accent">UEN No:</span> 201104417K</p>
  </div>
</section>

</body>
</html>
```